TL - business card

Tallow Partners is an insurance brokerage firm, inovative, proactive, vigorous, which aims to become the leader of the insurance brokers in Anfrica. We should like to get some designs which should be avoided also in Gray / Metallic for the Administration and Orange / Blue for the Managers (ike in the picture sent). The Blue / Green logo is not the correct one, but the source of the file. Please adjust the color accordingly for the business cards. 1 / Orange / Blue 2 / Gray / Metallic We want something classic but which is transmitted strenght, inovation, modernity and most of all, rapidity. We want something start-up like, very punchy and catching eye remaining profesional at the same time. Name: Dorian Whitlock Function: Managing Director Address: N ° 17/18 Rua Veloso - R / C 2B Direita - Bairro Mutamba - Luanda Tel: (+244) 947 582 316 Email: dorian.whitlock@tallow-p.example Website: www.tallow-p. example We want classic in the front and creative, colorfull at the back. The cards will be printed in relief, with very high quality of paper.
Insurance Broker
Colors
Designer to choose colors to be used in the design.

```html
<!DOCTYPE html>
<html lang="en">
<head>
<meta charset="utf-8">
<title>Tallow Partners – Business Card</title>
<link rel="stylesheet" href="https://fonts.googleapis.com/css2?family=Montserrat:wght@400;600&display=swap">
<style>
  :root {
    --backdrop: #d4d4d4;
    --brand-green: #0f9647;
    --brand-blue: #2aa5df;
    --ink-grey: #6b6b6b;
    --paper: #ffffff;
    --card-radius: 22px;
  }
  * { box-sizing: border-box; margin: 0; padding: 0; }
  html, body {
    width: 1200px; height: 930px; overflow: hidden;
    background: var(--backdrop);
    font-family: "Montserrat", sans-serif;
  }
  .canvas { position: relative; width: 1200px; height: 930px; }

  .card {
    position: absolute;
    width: 560px; height: 320px;
    border-radius: var(--card-radius);
    box-shadow: 0 8px 24px rgba(0,0,0,0.18);
    overflow: hidden;
  }

  /* Back side */
  .card-back {
    left: 90px; top: 110px;
    background: var(--brand-green);
    display: flex; align-items: center; justify-content: center; gap: 14px;
  }
  .card-back .brand-dot {
    width: 22px; height: 22px; border-radius: 50%;
    background: var(--paper);
  }
  .card-back .brand-name {
    color: var(--paper); font-weight: 600; font-size: 30px;
  }

  /* Front side */
  .card-front {
    left: 550px; top: 490px;
    background: var(--paper);
  }
  .front-brand {
    position: absolute; right: 36px; top: 44px;
    display: flex; align-items: center; gap: 10px;
  }
  .front-brand .brand-dot {
    width: 16px; height: 16px; border-radius: 50%;
    background: var(--brand-green);
  }
  .front-brand .brand-name {
    color: var(--brand-green); font-weight: 600; font-size: 24px;
  }
  .rule { position: absolute; height: 1px; background: var(--brand-blue); }
  .rule-top { left: 270px; right: 30px; top: 118px; }
  .rule-bottom { left: 34px; right: 30px; top: 250px; }

  .address {
    position: absolute; right: 30px; top: 132px;
    text-align: right; color: var(--ink-grey);
    font-size: 13px; line-height: 1.45;
  }

  .identity-tab {
    position: absolute; left: 0; top: 196px;
    width: 7px; height: 38px; background: var(--brand-blue);
  }
  .identity { position: absolute; left: 30px; top: 192px; }
  .identity .person-name {
    color: var(--brand-blue); font-weight: 600; font-size: 24px; line-height: 1.1;
  }
  .identity .person-role {
    color: var(--ink-grey); font-size: 13px; margin-top: 2px;
  }

  .contacts {
    position: absolute; left: 40px; top: 264px;
    list-style: none; color: var(--ink-grey); font-size: 13px; line-height: 1.6;
  }
  .contacts li { display: flex; align-items: center; gap: 9px; }
  .contacts svg { width: 11px; height: 11px; fill: none; stroke: var(--brand-blue); stroke-width: 1.6; }
</style>
</head>
<body>
<main class="canvas">

  <section class="card card-back" aria-label="Card back">
    <span class="brand-dot"></span>
    <span class="brand-name">Tallow Partners</span>
  </section>

  <section class="card card-front" aria-label="Card front">
    <div class="front-brand">
      <span class="brand-dot"></span>
      <span class="brand-name">Tallow Partners</span>
    </div>

    <div class="rule rule-top"></div>

    <address class="address" style="font-style:normal">
      N° 17/18 Rua Veloso<br>
      R / C 2B Direita<br>
      Bairro Mutamba - Luanda
    </address>

    <div class="identity-tab"></div>
    <div class="identity">
      <p class="person-name">Dorian Whitlock</p>
      <p class="person-role">Managing Director</p>
    </div>

    <div class="rule rule-bottom"></div>

    <ul class="contacts">
      <li>
        <svg viewBox="0 0 12 12" aria-hidden="true"><path d="M2.5 1.5l2 2-1 1.2c.7 1.5 1.8 2.6 3.3 3.3l1.2-1 2 2-1.3 1.5C5.5 10.3 1.7 6.5 1 3z"/></svg>
        (+244) 947 582 316
      </li>
      <li>
        <svg viewBox="0 0 12 12" aria-hidden="true"><rect x="1" y="2.5" width="10" height="7"/><path d="M1 2.5l5 4 5-4"/></svg>
        dorian.whitlock@tallow-p.example
      </li>
    </ul>
  </section>

</main>
</body>
</html>
```